Powerpoint design template for LUMOTEX for new digital platform

We would like to use a PowerPoint template, we would like to create a new page, we would like to create a new digital platform LUMOTEX for schools and parents for the creation of playful communication and educational tools for children to enhance their positive development, amaze them learn in a playful way. This platform is going to be the most creative, stimulating and innovative classroom, easy to use and fast to implement. Scrapbooking, collages ... Magazine, newsletters Diplomla / awards Slideshows Facebook Calendars Organizers Greetings Games ... This powerpoint template will be used essential to We are looking for a professional design, positioning our brand in the children market with an adult hearing. so you will need to find a good deal. Primary target: nurseries & schools from 0 to 18 years old and universities (in 2nd phase) Secondary target: small & medium businesses Third target: general public, and TPE If it is a color scheme, then it is suggested that it be marketed in Europe (UK, Italy, Spain) and in a 2nd Stage USA and other countries. multiple options for front page, insidious pages (multiple styles with limited text and extended text) and final contact page We need something to read, we can not do it too much, but we can not do it. , and inside pages aligned to our logo

Target Market(s)

Target 1; Education with teacher Target 2; parents and grandparents

Industry/Entity Type

Education

Font styles to use
Other font styles liked:
• not decided. but not too fancy

Requirements
Must have
• Multi page options for front page, page insides (multiple styles with limited text and extended text) and final page contact
Nice to have
• do not have a lot of ideas. We need something to read, we can not get away from it
Should not have
• not too fancy and busy: keep clarity & simplicity while reassuring on quality

```html
<!DOCTYPE html>
<html lang="en">
<head>
<meta charset="utf-8">
<title>LUMOTEX – Content Slide</title>
<link href="https://fonts.googleapis.com/css2?family=Open+Sans:wght@400;600;700&display=swap" rel="stylesheet">
<style>
  :root {
    --orange: #e88c34;
    --orange-deep: #dd7a22;
    --panel: #f8f68a;
    --ink: #1c1c1c;
    --white: #ffffff;
    --lime: #b7d334;
    --art-light: #fbf3e6;
    --art-warm: #f3c88f;
  }
  * { margin: 0; padding: 0; box-sizing: border-box; }
  html, body { width: 1200px; height: 900px; overflow: hidden; }
  body { background: var(--white); font-family: "Open Sans", Arial, sans-serif; }

  .slide {
    position: relative;
    width: 1200px;
    height: 900px;
    background: var(--orange);
    overflow: hidden;
  }

  .kids-art {
    position: absolute;
    left: 0; top: 0;
    width: 252px; height: 900px;
    background: linear-gradient(180deg, var(--art-light) 0%, var(--art-warm) 30%, var(--art-light) 55%, var(--art-warm) 80%, #e9a36a 100%);
  }

  .edge-stripes {
    position: absolute;
    left: 244px; top: 0;
    width: 72px; height: 900px;
  }

  .slide-title {
    position: absolute;
    left: 345px; top: 48px;
    color: var(--white);
    font-size: 33px;
    font-weight: 600;
    letter-spacing: 0.2px;
  }

  .brand {
    position: absolute;
    right: 24px; top: 36px;
    display: flex;
    flex-direction: column;
    align-items: flex-start;
  }
  .brand-row { display: flex; align-items: center; gap: 10px; }
  .brand-mark { width: 26px; height: 26px; background: var(--lime); }
  .brand-name {
    color: var(--ink);
    font-size: 36px;
    font-weight: 700;
    line-height: 1;
  }
  .brand-tagline {
    margin-top: 6px;
    margin-left: 36px;
    color: var(--ink);
    font-size: 8px;
    font-weight: 400;
    letter-spacing: 2px;
    line-height: 1.3;
    width: 110px;
  }

  .content-panel {
    position: absolute;
    left: 345px; top: 135px;
    width: 855px; height: 710px;
    background: var(--panel);
    padding: 57px 0 0 47px;
  }

  .topic { width: 760px; margin-bottom: 49px; }
  .topic-heading {
    color: var(--ink);
    font-size: 30px;
    font-weight: 600;
    line-height: 1.2;
    margin-bottom: 2px;
  }
  .topic-body {
    color: var(--ink);
    font-size: 23.5px;
    font-weight: 400;
    line-height: 33px;
  }
</style>
</head>
<body>
<div class="slide">
  <div class="kids-art" role="img" aria-label="Illustration of cheerful cartoon children peeking in from the left edge, holding a pencil and an alphabet block"></div>

  <svg class="edge-stripes" viewBox="0 0 72 900" aria-hidden="true">
    <rect x="0" y="0" width="72" height="900" fill="var(--orange)"/>
    <rect x="4" y="0" width="5" height="900" fill="var(--white)"/>
    <rect x="13" y="0" width="3" height="900" fill="var(--white)"/>
    <rect x="24" y="0" width="6" height="900" fill="var(--white)"/>
    <rect x="40" y="0" width="3" height="900" fill="var(--white)"/>
    <rect x="52" y="0" width="5" height="900" fill="var(--white)"/>
    <rect x="64" y="0" width="2" height="900" fill="var(--orange-deep)"/>
  </svg>

  <h1 class="slide-title">Cotnent TItele Here</h1>

  <div class="brand">
    <div class="brand-row">
      <span class="brand-mark"></span>
      <span class="brand-name">LUMOTEX</span>
    </div>
    <p class="brand-tagline">YOUR TAGLINE GOES HERE</p>
  </div>

  <main class="content-panel">
    <section class="topic">
      <h2 class="topic-heading">Subtext here</h2>
      <p class="topic-body">Lemon drops oat cake oat cake sugar plum sweet gingerbread chocolate cake gingerbread. Lemon drops oat cake oat cake sugar plum sweet</p>
    </section>
    <section class="topic">
      <h2 class="topic-heading">Subtext here</h2>
      <p class="topic-body">Lemon drops oat cake oat cake sugar plum sweet gingerbread chocolate cake gingerbread. Lemon drops oat cake oat cake sugar plum sweet</p>
    </section>
    <section class="topic">
      <h2 class="topic-heading">Subtext here</h2>
      <p class="topic-body">Lemon drops oat cake oat cake sugar plum sweet gingerbread chocolate cake gingerbread. Lemon drops oat cake oat cake sugar plum sweet</p>
    </section>
  </main>
</div>
</body>
</html>
```